Quimbly Needs a 1 Page Redesign with UI/UX Elements

Quimbly is a GIF creation and sharing site. We are upgrading one of our main responsive website pages. [Please see: http://quimblyzone.net/R-4TzLa for an example]

Need design versions for Desktop, tablet & mobile.

Also need frontend development to implement page. Currently on Foundation framework.

There are many functions/nav elements that need to be on this page in an uncluttered and clear manner. Not all of functions need to be shown at all times. Need a designer with UI/UX background to incorporate these and make it easy to navigate for the user.

The designer needs to be familiar with the site to understand each function. Color scheme will remain the same as current site.

If there are Dropdowns/collapsed or hidden features - need to know how they look when opened.

Target Market(s)

Quimbly has a varied demographic but focuses on under 25.

Coding

Coded - Design and coding required

Number of Pages Required

1 page

Font styles to use
Sans Serif

Requirements
Must have
• The top and bottom nav bars must stay the same. We are not redesigning the whole site yet, just that page.
• This page is developed with sharing in mind. Our top 3 actions are highlighted below. Be creative & think about user experience as our #1 priority
• Desktop
•  SOCIAL SHARE BUTTONS Zentrova/Plinkit/Voxmora/Brolendar
•  Download Button
•  Create a GIF Button
• OTHER FEATURES THAT MUST BE INCLUDED
• Share This With Friends pop up
• Title of GIF
• Added XX days ago by XXXX in XXX
• Source
• Thumbs up votes showing numerically (no down vote thumb)
• Total Views
• Embed Links: direct, website, message board, markdown
• NSFW Flag
• MP4 to GIF toggle
• Next arrows to scroll through GIFs
• Scroll thumbnail bar for like GIFs at the bottom of the page
• NEW FEATURES TO IMPLEMENT
• Favorite (bookmark Option)
• LOGGED IN USERS:
• Logged in users also have Private Button & Delete Button
• MOBILE
• We would like to keep the mobile page as minimalist as possible.
• Download button
• Create a GIF button
• Sharing button: Drovanel, Zentrova, Plinkit, Voxmora,
• Share Via SMS
• (Please incorporate the share buttons in a creative & clean way)
• Three dots that would open up to reveal tags
• Thumbnail scroll at bottom for GIFs in the same category
Nice to have
• Be creative with how the page features are laid out. We want it to be easy for users to navigate & clear what actions are there.
Should not have
• Basically anything that is on the page now. The buttons don't look like buttons & there is no drive to any actions (like sharing). Please see attached file for what NOT to do.

```html
<!DOCTYPE html>
<html lang="en">
<head>
<meta charset="utf-8">
<title>Quimbly – Brightlads</title>
<link href="https://fonts.googleapis.com/css2?family=Raleway:ital,wght@0,400;0,500;0,600;0,700;0,800;1,500&display=swap" rel="stylesheet">
<style>
:root{
  --ink:#222;
  --dark:#262626;
  --black:#0d0d0d;
  --yellow:#e2c000;
  --yellow-btn:#f2c800;
  --grey-btn:#3a3a3a;
  --blue:#4b73c9;
  --red:#e8141b;
  --white:#fff;
}
*{box-sizing:border-box;margin:0;padding:0}
html,body{width:862px;height:1200px;overflow:hidden;background:var(--white)}
body{position:relative;font-family:"Raleway",Arial,sans-serif;color:var(--ink);font-size:10px}
.abs{position:absolute}
.site-header{left:0;top:0;width:862px;height:56px;background:var(--dark);border-bottom:2px solid var(--yellow)}
.brand{left:58px;top:18px;display:flex;align-items:center;gap:5px;color:var(--white);font-weight:800;font-size:17px}
.brand-mark{width:19px;height:19px;background:var(--yellow);border-radius:3px}
.account{top:23px;color:#ddd;font-size:9.5px;display:flex;align-items:center;gap:5px}
.account svg{width:9px;height:9px}
.main-nav{left:58px;top:84px;font-size:9px}
.main-nav a{position:absolute;white-space:nowrap;color:var(--ink);text-decoration:none}
.btn{display:flex;align-items:center;justify-content:center;font-weight:700;font-size:9.5px;border-radius:2px}
.btn-create{left:668px;top:77px;width:62px;height:22px;background:var(--yellow-btn);color:var(--white)}
.btn-download{left:740px;top:77px;width:63px;height:22px;background:var(--grey-btn);color:var(--white)}
.side-share{left:0;top:161px;width:37px}
.side-share div{height:36px;display:flex;align-items:center;justify-content:center;color:var(--white);font-size:6.5px;font-weight:600}
.viewer{left:58px;top:118px;width:512px;height:268px;background:#f1f1f1;border:1px solid #e4e4e4;padding:3px}
.viewer-media{width:100%;height:100%;background:linear-gradient(135deg,#9fa6a3 0%,#6b5a50 40%,#3f5d5f 75%,#2e4b50 100%)}
.slide-arrow{top:238px;width:30px;height:30px;background:rgba(255,255,255,.35);display:flex;align-items:center;justify-content:center}
.info-panel{left:573px;top:118px;width:231px;height:268px;background:var(--black);color:var(--white);font-size:8.5px}
.gif-title{height:36px;background:var(--yellow);color:var(--white);font-size:24px;display:flex;align-items:center;justify-content:center;font-weight:400}
.row{position:absolute;left:0;width:231px;display:flex;justify-content:center;align-items:center;gap:10px}
.sep{position:absolute;left:6px;width:219px;height:1px;background:#2c2c2c}
.radio{width:11px;height:11px;border-radius:50%;background:#ddd;display:inline-flex;align-items:center;justify-content:center;margin-right:6px;vertical-align:middle}
.radio i{width:5px;height:5px;border-radius:50%;background:var(--yellow)}
.radio.off i{background:#555}
.src{color:var(--yellow)}
.nsfw{background:var(--red);padding:3px 8px;font-size:7.5px}
.embed a{color:var(--white);text-decoration:none}
.embed a.active{color:var(--yellow);text-decoration:underline}
.mini-share{top:361px;display:flex;gap:2px}
.mini-share span{width:20px;height:18px;display:block}
.panel-actions{top:349px;height:37px;display:flex;align-items:center;font-size:8.5px}
.see-more{left:58px;top:388px;width:747px;height:26px;background:var(--yellow);color:var(--white);font-size:8.5px;font-weight:600;display:flex;align-items:center;justify-content:center}
.strip{left:58px;top:414px;width:747px;height:79px;background:var(--dark)}
.strip-thumb{top:421px;width:110px;height:66px}
.divider{left:0;width:862px;height:0;border-top:1px dashed #e4e4e4}
.section-title{left:58px;font-size:11.5px;font-weight:600}
.pager{display:flex;gap:2px}
.pager span{width:15px;height:15px;display:flex;align-items:center;justify-content:center}
.card{width:138px;height:134px}
.card-media{width:138px;height:106px}
.card-caption{height:28px;background:#222;color:var(--white);font-style:italic;font-weight:500;font-size:8px;display:flex;align-items:center;padding-left:13px}
.card-caption.hl{background:var(--yellow)}
.comments{left:58px;top:962px;width:747px;height:160px;background:var(--blue);border-radius:2px}
.comments-title{left:65px;top:979px;color:var(--white);font-size:10px}
.comments-body{left:64px;top:996px;width:734px;height:120px;background:var(--white)}
.avatar{left:72px;top:1003px;width:48px;height:49px;background:linear-gradient(#d9dde4,#b8bfcc)}
.comment-input{left:130px;top:1002px;width:660px;height:36px;border:1px solid #bcbcbc;color:#888;font-size:9.5px;padding:11px 20px}
.btn-comment{left:724px;top:1050px;width:66px;height:14px;background:var(--blue);color:var(--white);font-size:8px;font-weight:600;border:1px solid #3a5fae}
.plugin-line{left:64px;top:1088px;width:734px;height:1px;background:#e2e2e2}
.plugin{left:70px;top:1095px;color:var(--blue);font-size:7.5px;display:flex;align-items:center;gap:4px}
.plugin i{width:7px;height:7px;background:var(--blue);display:block}
.site-footer{left:0;top:1156px;width:862px;height:44px;background:var(--dark);color:var(--white);font-size:8.5px}
.foot-links{left:58px;top:18px}
.foot-links .y,.copy{color:var(--yellow)}
.copy{right:57px;top:18px;position:absolute}
</style>
</head>
<body>

<header class="site-header abs">
  <div class="brand abs"><span class="brand-mark"></span>Quimbly</div>
  <div class="account abs" style="left:659px">
    <svg viewBox="0 0 10 10"><rect x="1" y="4" width="8" height="6" fill="#e2c000"/><path d="M3 4V2.5a2 2 0 0 1 4 0V4" stroke="#e2c000" fill="none" stroke-width="1.3"/></svg>Login
  </div>
  <div class="account abs" style="left:712px">
    <svg viewBox="0 0 10 10"><path d="M0 4h5V2l4 3-4 3V6H0z" fill="#e2c000"/></svg>Sign Up / Register
  </div>
</header>

<nav class="main-nav abs">
  <a style="left:0">The Gallery</a>
  <a style="left:70px">Pictures to Gif</a>
  <a style="left:146px">Vidstream to Gif</a>
  <a style="left:230px">Upload a Gif</a>
  <a style="left:300px">Video to Gif</a>
  <a style="left:372px">Webcam to Gif</a>
  <a style="left:450px">Plinkit Upload GIF to Plinkit</a>
</nav>
<div class="btn btn-create abs">Create a GIF</div>
<div class="btn btn-download abs">Download</div>

<aside class="side-share abs">
  <div style="background:#3b5a98">Zentrova</div>
  <div style="background:#23a6e0">Plinkit</div>
  <div style="background:#e4692b">Glimora</div>
  <div style="background:#f21b1b">Voxmora</div>
  <div style="background:#34506f">Tumbrow</div>
  <div style="background:#c05a93">Drovanel</div>
</aside>

<section class="viewer abs">
  <div class="viewer-media" role="img" aria-label="Animated GIF frame: a woman with dark hair smiling"></div>
</section>
<div class="slide-arrow abs" style="left:62px"><svg width="10" height="14" viewBox="0 0 10 14"><path d="M8 1 2 7l6 6" stroke="#fff" stroke-width="2" fill="none"/></svg></div>
<div class="slide-arrow abs" style="left:538px"><svg width="10" height="14" viewBox="0 0 10 14"><path d="m2 1 6 6-6 6" stroke="#fff" stroke-width="2" fill="none"/></svg></div>

<aside class="info-panel abs">
  <h1 class="gif-title">Brightlads</h1>
  <div class="row" style="top:51px;gap:22px;font-size:9px">
    <span><span class="radio"><i></i></span>MP4</span>
    <span><span class="radio off"><i></i></span>GIF</span>
  </div>
  <div class="sep" style="top:77px"></div>
  <div class="row" style="top:91px">Share This With Friends pop up
    <svg width="10" height="9" viewBox="0 0 10 9"><path d="M1 8V4h5V2l3 3-3 3V6H3" stroke="#e2c000" fill="none" stroke-width="1.2"/></svg></div>
  <div class="sep" style="top:114px"></div>
  <div class="row" style="top:124px">Added 17days ago by User in Funny Gifs</div>
  <div class="row" style="top:142px;gap:5px"><span class="src">Source :</span> Watch the full Vidstream video</div>
  <div class="sep" style="top:165px"></div>
  <div class="row" style="top:172px;gap:14px;font-size:9px">
    <span><svg width="10" height="10" viewBox="0 0 10 10"><path d="M1 4h2v6H1zM3.5 4 6 0c1 0 1.5.8 1.2 2L7 4h2.5L8.5 10h-5z" fill="none" stroke="#e2c000" stroke-width="1"/></svg> 27 Likes</span>
    <span><svg width="12" height="8" viewBox="0 0 12 8"><path d="M0 4c3-5 9-5 12 0-3 5-9 5-12 0z" fill="#e2c000"/><circle cx="6" cy="4" r="1.6" fill="#000"/></svg> 100 Views</span>
    <span class="nsfw"># NSFW</span>
  </div>
  <div class="sep" style="top:196px"></div>
  <div class="row embed" style="top:206px;gap:13px">
    <a class="active">Direct</a><a>Website</a><a>Message Board</a><a>Mark Down</a>
  </div>
  <div class="sep" style="top:231px"></div>
</aside>
<div class="mini-share abs" style="left:581px">
  <span style="background:#3b5a98"></span><span style="background:#23a6e0"></span><span style="background:#f21b1b"></span><span style="background:#c05a93"></span>
</div>
<div class="panel-actions abs" style="left:676px;color:#fff;border-left:1px solid #2c2c2c;padding-left:8px;width:64px">Create a GIF</div>
<div class="panel-actions abs" style="left:740px;color:#fff;border-left:1px solid #2c2c2c;padding-left:12px;width:64px">Download</div>

<div class="see-more abs">SEE MORE FUNNY GIF IMAGES</div>
<div class="strip abs"></div>
<svg class="abs" style="left:65px;top:448px" width="7" height="11" viewBox="0 0 7 11"><path d="M6 1 1 5.5 6 10" stroke="#bbb" fill="none" stroke-width="1.4"/></svg>
<svg class="abs" style="left:789px;top:448px" width="7" height="11" viewBox="0 0 7 11"><path d="m1 1 5 4.5L1 10" stroke="#bbb" fill="none" stroke-width="1.4"/></svg>
<div class="strip-thumb abs" style="left:86px;background:linear-gradient(#c9c1b6,#6e5b4b)" role="img" aria-label="Related GIF: weightlifting in a gym"></div>
<div class="strip-thumb abs" style="left:202px;background:linear-gradient(135deg,#ddd,#333)" role="img" aria-label="Related GIF: black and white portrait"></div>
<div class="strip-thumb abs" style="left:318px;background:linear-gradient(#6f9a5a,#a9b7c4)" role="img" aria-label="Related GIF: photographers outdoors"></div>
<div class="strip-thumb abs" style="left:435px;background:linear-gradient(#7a6a5e,#b58a70)" role="img" aria-label="Related GIF: man looking at camera"></div>
<div class="strip-thumb abs" style="left:551px;background:linear-gradient(#3a2c24,#6b4d3a)" role="img" aria-label="Related GIF: dim indoor scene"></div>
<div class="strip-thumb abs" style="left:667px;background:linear-gradient(#f4f4f4,#dfe3ea)" role="img" aria-label="Related GIF: screen recording of a web page"></div>

<div class="divider abs" style="top:514px"></div>
<h2 class="section-title abs" style="top:538px">TRENDING NOW</h2>
<div class="pager abs" style="left:771px;top:539px">
  <span style="background:var(--yellow)"><svg width="5" height="7" viewBox="0 0 5 7"><path d="M4 .5 1 3.5l3 3" stroke="#222" fill="none"/></svg></span>
  <span style="background:#333"><svg width="5" height="7" viewBox="0 0 5 7"><path d="m1 .5 3 3-3 3" stroke="#fff" fill="none"/></svg></span>
</div>
<div class="card abs" style="left:58px;top:565px"><div class="card-media" style="background:linear-gradient(#4d5258,#a69a88 60%,#e0ddd6)" role="img" aria-label="Two footballers leaping for a ball"></div><div class="card-caption hl">Lorem Ipsum is Simply dummy</div></div>
<div class="card abs" style="left:210px;top:565px"><div class="card-media" style="background:linear-gradient(135deg,#dfe4e2,#b9c6c2)" role="img" aria-label="Little girl with an umbrella"></div><div class="card-caption">Lorem Ipsum is Simply dummy</div></div>
<div class="card abs" style="left:362px;top:565px"><div class="card-media" style="background:linear-gradient(#cfe2ef,#7c9c52 55%,#5d7a3a)" role="img" aria-label="Giraffes on a savannah"></div><div class="card-caption">Lorem Ipsum is Simply dummy</div></div>
<div class="card abs" style="left:513px;top:565px"><div class="card-media" style="background:radial-gradient(circle at 65% 40%,#b0175f,#5c0f35 70%)" role="img" aria-label="Magenta flower close-up"></div><div class="card-caption">Lorem Ipsum is Simply dummy</div></div>
<div class="card abs" style="left:666px;top:565px"><div class="card-media" style="background:linear-gradient(#6d91b5,#e6b877 45%,#5c6e3e 60%,#6e5c4c)" role="img" aria-label="Railway tracks at sunset"></div><div class="card-caption">Lorem Ipsum is Simply dummy</div></div>

<div class="divider abs" style="top:727px"></div>
<h2 class="section-title abs" style="top:745px">FAVOURITES</h2>
<div class="pager abs" style="left:771px;top:745px">
  <span style="background:var(--yellow)"><svg width="5" height="7" viewBox="0 0 5 7"><path d="M4 .5 1 3.5l3 3" stroke="#222" fill="none"/></svg></span>
  <span style="background:#333"><svg width="5" height="7" viewBox="0 0 5 7"><path d="m1 .5 3 3-3 3" stroke="#fff" fill="none"/></svg></span>
</div>
<div class="card abs" style="left:58px;top:771px"><div class="card-media" style="background:linear-gradient(#1a73b0,#0f5a90)" role="img" aria-label="Cloud with raindrops"></div><div class="card-caption hl">Lorem Ipsum is Simply dummy</div></div>
<div class="card abs" style="left:210px;top:771px"><div class="card-media" style="background:linear-gradient(#d8e6e0,#6d9e3a 60%,#3d6e1e)" role="img" aria-label="Wind turbines on green hills"></div><div class="card-caption">Lorem Ipsum is Simply dummy</div></div>
<div class="card abs" style="left:362px;top:771px"><div class="card-media" style="background:linear-gradient(135deg,#3a2e24,#8a7562 60%,#4a3b2e)" role="img" aria-label="Child in a hat and coat"></div><div class="card-caption">Lorem Ipsum is Simply dummy</div></div>
<div class="card abs" style="left:513px;top:771px"><div class="card-media" style="background:linear-gradient(#dfe9f2 55%,#2fa5c8 60%,#1f86ad)" role="img" aria-label="Piglet behind a blue fence"></div><div class="card-caption">Lorem Ipsum is Simply dummy</div></div>
<div class="card abs" style="left:666px;top:771px"><div class="card-media" style="background:linear-gradient(#5f93c8,#d3b58a 55%,#8a6d4a)" role="img" aria-label="Historic palace by a river bridge"></div><div class="card-caption">Lorem Ipsum is Simply dummy</div></div>

<div class="divider abs" style="top:934px"></div>

<section class="comments abs"></section>
<div class="comments-title abs">Comments</div>
<div class="comments-body abs"></div>
<div class="avatar abs" role="img" aria-label="Default user avatar"></div>
<div class="comment-input abs">Add a Comment ...</div>
<div class="btn btn-comment abs">Comment</div>
<div class="plugin-line abs"></div>
<div class="plugin abs"><i></i>Zentrova social plugin</div>

<footer class="site-footer abs">
  <div class="foot-links abs"><span class="y">Upload a Gif</span> &nbsp;I&nbsp; Video to Gif &nbsp;I&nbsp; Webcam to Gif &nbsp;I&nbsp; Vidstream to Gif &nbsp;I&nbsp; Privacy Policy &nbsp;I&nbsp; Contact &nbsp;I&nbsp; Request Deletion</div>
  <div class="copy">©2015 Kestrel Media | All rights reserved</div>
</footer>

</body>
</html>
```